KRL Stationery Design Project

Dear Designers,
We need a new stationery design for company to match our new logo.
Designers should provide a design for the following:
1. Business Card: 3.5x2 Inches.
2. Letterhead: A4 size.
3. Envelops: 25x35.5 Cm.
You can keep the Arabic name at the bottom of the logo Or you can use the separate attached Arabic Name.
Please refer to the attached logo guide for design information.
Sample Business Card information:
Name: Tarek Sowan
Position: Operation Manager
Tel: +966 920007164 Ex. 500
Fax: +966 (3)8842617
Mob: +966 (5)00263817
email: tarek@krl-example.com.sa
URL: www.krl-example.com.sa
Address:
Nakheel Heights, Suite 718
Zayed bin Omar Str.
Khobar, 31847
Saudi Arabia
Updates
Dear All,
Please note, we had uploaded our logo along with Arabic writing in Adobe illustrator format (.ai).
Regards,
Karim
Dear All,
A sample data for the business card had been added as per your request.
Regards,
Karim

```html
<!DOCTYPE html>
<html lang="en">
<head>
<meta charset="utf-8">
<title>KRL Business Card</title>
<link rel="stylesheet" href="https://fonts.googleapis.com/css2?family=Open+Sans:ital,wght@0,400;0,700;1,700&display=swap">
<style>
  :root {
    --navy: #142f52;
    --grey: #9a9b9e;
    --ink: #3a3a3a;
    --paper: #ffffff;
    --backdrop: #2a2a2a;
  }
  * { box-sizing: border-box; margin: 0; padding: 0; }
  html, body { width: 960px; height: 1200px; overflow: hidden; }
  body {
    background: var(--backdrop);
    font-family: "Open Sans", Arial, sans-serif;
    position: relative;
  }
  .card {
    position: absolute;
    left: 57px;
    width: 840px;
    height: 478px;
    background: var(--paper);
    border-radius: 28px;
    overflow: hidden;
  }
  .card--front { top: 97px; }
  .card--back { top: 625px; }
  .card__wave { position: absolute; left: 0; top: 0; width: 840px; height: 180px; }
  .holder {
    position: absolute;
    right: 29px;
    top: 54px;
    text-align: right;
    color: var(--paper);
  }
  .holder__name { font-size: 25px; line-height: 32px; }
  .holder__role { font-size: 19px; line-height: 28px; }
  .brand {
    position: absolute;
    display: flex;
    align-items: center;
    color: var(--navy);
    font-weight: 700;
  }
  .brand__mark { background: var(--navy); display: block; }
  .card--front .brand { left: 60px; top: 205px; font-size: 110px; gap: 24px; }
  .card--front .brand__mark { width: 58px; height: 58px; }
  .card--back .brand { left: 0; right: 0; top: 150px; justify-content: center; font-size: 160px; gap: 34px; }
  .card--back .brand__mark { width: 84px; height: 84px; }
  .address, .contact {
    position: absolute;
    bottom: 28px;
    font-size: 18.5px;
    line-height: 28px;
    color: var(--ink);
  }
  .address { left: 34px; }
  .contact { right: 29px; text-align: right; }
  .contact__label { font-weight: 700; font-style: italic; }
  .contact__sep { padding: 0 8px; }
</style>
</head>
<body>
  <section class="card card--front">
    <svg class="card__wave" viewBox="0 0 840 180" aria-hidden="true">
      <path d="M0,0 H840 V122 C650,150 430,122 270,78 C160,50 70,48 0,58 Z" fill="var(--navy)"/>
      <path d="M0,72 C80,60 170,64 280,94 C440,138 640,160 840,132 V142 C640,178 430,162 280,120 C170,90 80,90 0,114 Z" fill="var(--grey)"/>
    </svg>
    <div class="holder">
      <p class="holder__name">Your Name</p>
      <p class="holder__role">Designation</p>
    </div>
    <div class="brand"><span class="brand__mark"></span><span class="brand__name">KRL</span></div>
    <address class="address" style="font-style:normal">
      1234, Suite# 123, Street Name<br>
      State Name, Country Code
    </address>
    <div class="contact">
      <p><span class="contact__label">t</span> : 123-123-1234<span class="contact__sep">|</span><span class="contact__label">f</span> : 123-123-1234</p>
      <p><span class="contact__label">e</span> : info@krl-example.com.sa</p>
      <p><span class="contact__label">w</span> : www.krl-example.com.sa</p>
    </div>
  </section>

  <section class="card card--back">
    <div class="brand"><span class="brand__mark"></span><span class="brand__name">KRL</span></div>
  </section>
</body>
</html>
```